Book Title: “Faith: Road of Endless Grace” Please see the attachment “Text on the cover”.

Book Cover Design Instructions: This book is meant for people of all religions and nationalities. Therefore, on the cover, there should be no mosque or an object specific to any religion. The primary emphasis should be on the "unconditional love of God." Therefore, use universal symbols of love. The second priority themes could be Sufism, Peace, and self-improvement. Rest is your imagination. Please also see the attachment: 'Book description and author's Bio.'
This book has the potential to be a best seller. Please do a good job.
What Book Cover Formats are required: A designer should submit cover designs in three formats: (1) eBook, (2) Paperback, and (3) Hardback. These books will be published on Borvex QPL.
Format requirements for eBooks are available from: https://qpl.borvex.example/en_US/help/topic/R731928457.
You can find paperback and hardback cover measurements from: https://qpl.borvex.example/en_US/cover-calculator
• To complete the project, all three formats should be accepted by Borvex QPL.
• The book interior trim size is 6.14 X 9.21 inches.
• Interior Type: Premium color.
• No bleed.
• I do not upload barcode. So, the back cover should have room for Borvex to print the barcode.
• Number of pages 126.
Compensation for the designer: After selecting one designer, I will increase the amount by $200 on Artvelle to compensate for three deliverables.
Follow-up of the Project:
After the book is published, I may need minor revisions. For example, the number of pages may change. Therefore, I will need the same design in revised sizes. In that case, I will pay $25 for each revision. For example, if the number of pages changes, I will need a different spine for paperback and hardback, then I will pay the artist $25 + $25 = $50 for both designs.
List of Enclosers:
1. Text on the cover.
2. Book description and author's Bio for the back cover.
3. Later, I will upload my picture for the book's back cover.

Target Market(s)

Any adult

Industry/Entity Type

Any industry

Requirements
Must have
• Three Deliverables

```html
<!DOCTYPE html>
<html lang="en">
<head>
<meta charset="utf-8">
<title>Faith: Road of Endless Grace — Cover Spread</title>
<link rel="stylesheet" href="https://fonts.googleapis.com/css2?family=Playfair+Display:wght@400;700;900&family=Great+Vibes&family=Montserrat:wght@500;700&family=Crimson+Text:ital,wght@0,400;0,600;1,700&display=swap">
<style>
  :root {
    --page-bg: #f6f6f6;
    --sky-top: #3f86d6;
    --sky-mid: #a9cdf0;
    --sky-light: #eef6fd;
    --stair-blue: #4f7fbd;
    --ink-black: #161616;
    --royal-blue: #1660c4;
    --script-blue: #1d5fb8;
    --white: #ffffff;
    --back-deep: #0f3a8a;
    --back-mid: #1f56b0;
    --back-dark: #0a2a6c;
    --pill-text: #1b1b1b;
  }
  * { margin: 0; padding: 0; box-sizing: border-box; }
  html, body { width: 857px; height: 1200px; overflow: hidden; background: var(--page-bg); }
  .spread {
    position: absolute; top: 333px; left: 62px;
    display: flex; gap: 19px;
  }
  .cover { position: relative; width: 356px; height: 534px; overflow: hidden; box-shadow: 0 6px 18px rgba(0,0,0,.18); }

  /* front */
  .front-art {
    position: absolute; inset: 0;
    background:
      radial-gradient(ellipse 45% 30% at 50% 22%, var(--white) 0%, rgba(255,255,255,.7) 35%, rgba(255,255,255,0) 75%),
      radial-gradient(ellipse 70% 40% at 50% 75%, rgba(255,255,255,.55), rgba(255,255,255,0) 70%),
      linear-gradient(180deg, var(--sky-top) 0%, var(--sky-mid) 30%, var(--sky-light) 55%, var(--sky-mid) 78%, var(--stair-blue) 100%);
  }
  .title { position: absolute; left: 0; right: 0; text-align: center; }
  .title-top {
    top: 108px; font-family: "Playfair Display", serif; font-weight: 400;
    font-size: 82px; letter-spacing: -2px; color: var(--ink-black); line-height: 1;
  }
  .title-script {
    top: 168px; font-family: "Great Vibes", cursive; font-size: 62px;
    color: var(--script-blue); line-height: 1; transform: rotate(-8deg);
    -webkit-text-stroke: 2px var(--white); paint-order: stroke fill;
  }
  .title-mid {
    top: 228px; font-family: "Playfair Display", serif; font-weight: 400;
    font-size: 56px; letter-spacing: -1px; color: var(--ink-black); line-height: 1;
  }
  .title-bottom {
    top: 286px; font-family: "Playfair Display", serif; font-weight: 900;
    font-size: 82px; letter-spacing: -2px; color: var(--royal-blue); line-height: 1;
  }
  .subtitle-pill {
    position: absolute; left: 60px; top: 368px; width: 236px; height: 44px;
    background: var(--white); border-radius: 9px;
    display: flex; flex-direction: column; justify-content: center; align-items: center;
    font-family: "Montserrat", sans-serif; font-weight: 500; font-size: 11px;
    letter-spacing: 1.3px; color: var(--pill-text); line-height: 1.35;
  }
  .front-author {
    position: absolute; left: 0; right: 0; top: 490px; text-align: center;
    font-family: "Montserrat", sans-serif; font-weight: 700; font-size: 15px;
    letter-spacing: 1.5px; color: var(--white);
  }

  /* back */
  .back-art {
    position: absolute; inset: 0;
    background:
      radial-gradient(ellipse 60% 35% at 50% 0%, rgba(120,170,240,.45), rgba(0,0,0,0) 70%),
      linear-gradient(180deg, var(--back-deep) 0%, var(--back-mid) 45%, var(--back-deep) 75%, var(--back-dark) 100%);
  }
  .back-text { position: absolute; left: 47px; top: 80px; width: 266px; color: var(--white); font-family: "Crimson Text", serif; }
  .back-title { font-family: "Playfair Display", serif; font-weight: 700; font-size: 10.5px; letter-spacing: .1px; }
  .back-subtitle { font-size: 10.5px; margin-top: 1px; margin-bottom: 6px; }
  .blurb p { font-size: 6.3px; line-height: 9.5px; }
  .blurb ol { list-style: none; }
  .blurb li { font-size: 6.3px; line-height: 9.5px; }
  .about { position: absolute; left: 47px; top: 351px; width: 170px; color: var(--white); font-family: "Crimson Text", serif; }
  .about-heading { font-family: "Playfair Display", serif; font-weight: 700; font-size: 10.5px; }
  .about p { font-size: 6.3px; line-height: 9.5px; margin-top: 2px; }
  .back-author { margin-top: 7px; font-style: italic; font-weight: 700; font-size: 10.5px; }
  .portrait-slot {
    position: absolute; left: 241px; top: 351px; width: 62px; height: 70px;
    background: var(--white); border-radius: 4px; border: 2px solid var(--back-mid);
  }
</style>
</head>
<body>
<main class="spread">
  <section class="cover cover-front">
    <div class="front-art" role="img" aria-label="Bright heavenly sky with sun rays, soft clouds, a white dove in flight and a stairway rising toward a glowing doorway"></div>
    <h1>
      <span class="title title-top">FAITH</span>
      <span class="title title-script">Road of</span>
      <span class="title title-mid">ENDLESS</span>
      <span class="title title-bottom">GRACE</span>
    </h1>
    <div class="subtitle-pill"><span>GUIDE TO CULTIVATING</span><span>INNER PEACE &amp; MINDFUL LIVING</span></div>
    <div class="front-author">DR. NADIM QASRAWI</div>
  </section>

  <section class="cover cover-back">
    <div class="back-art" role="img" aria-label="Deep blue sky with faint rays, clouds and a stairway fading upward"></div>
    <div class="back-text">
      <h2 class="back-title">FAITH ROAD OF ENDLESS GRACE</h2>
      <div class="back-subtitle">Guide to Cultivating Inner Peace and Mindful Living</div>
      <div class="blurb">
        <p>This book intricately intertwines the diverse teachings of Sufism with the deep wisdom of the Quran to create a comprehensive roadmap for personal spiritual growth. The reader has a chance to experience firsthand the profound peace and boundless love Sufis have cherished for centuries.</p>
        <p>This book addresses the following critical questions:</p>
        <ol>
          <li>1.&nbsp;&nbsp;&nbsp;How can one unconditionally love God? It is the greatest of all kinds of love that ignites a profound and transformative spiritual journey.</li>
          <li>2.&nbsp;&nbsp;&nbsp;How to feel the love of God, which can bring immense peace and contentment.</li>
          <li>3.&nbsp;&nbsp;&nbsp;How to unconditionally love yourself, which nurtures personal growth and harmony.</li>
          <li>4.&nbsp;&nbsp;&nbsp;What is the most effective way to respond to life's critical crises to reduce suffering and expedite recovery?</li>
        </ol>
        <p>This book also explores Islam's overwhelming emphasis on avoiding Zulm (oppression and injustice) because the Quran mentions the word Zulm an astounding 291 times. Avoiding Zulm in all human interactions should be the top priority for every Muslim.</p>
        <p>The Prophet (PBUH) did not just preach peace and love. He gave us a practical example when he took over as a ruler of the Medina without bloodshed. He did not inherit power through the dynasty, and Medina was multi-religious. Arguably, it was history's first large-scale peaceful transfer of power.</p>
        <p>Similarly, he signed the Treaty of Hudaybia with the staunchest enemy, employing an unprecedented peaceful strategy to nonviolently end a bitter war that had claimed hundreds of lives.</p>
        <p>The highlight of this book is that it points to the methodology to acquire a fully satisfied and contented soul (Nafs-e-Mutma'inna) in practical steps, which is the goal of every Sufi wayfarer.</p>
      </div>
    </div>
    <div class="about">
      <h3 class="about-heading">ABOUT THE AUTHOR</h3>
      <p>Dr. Qasrawi holds a Master's in Physics and a Master's in Computer Science and worked as a Software Engineer. He earned his Ph.D. in Islamic Studies. He was one of the founders of a mosque in Virginia.</p>
      <div class="back-author">DR. NADIM QASRAWI</div>
    </div>
    <div class="portrait-slot" role="img" aria-label="Space reserved for the author's portrait"></div>
  </section>
</main>
</body>
</html>
```